I have a logo and need to design the business card and stationery.
Updates

The uploaded logo image named as GREYMARSH CONSTRUCTION which is to be replaced to GREYMARSH CONTRACTS. Kindly add below details and submit the designs- Company name- Greymarsh Engineering Contracts LLP Name & Post- Kelvan Joshi (Designated Partner) Address- Block No.317, Wing C, Tulvo Trade Court, Manek Pural Road, Ruparel Industrial Estate, Goregaon(E), Mumbai - 400 063 Contact- +91 97415 60382 Email- kelvanjoshi@mailbrook.example Website- www.greymarshcontracts.example Contact for Letterhead- +91-22-28754193

Hi Tovin Rahul, We are liking your Design #28860835. We have suggested some changes which are mentioned in feedback. Kindly revert with it asap to finalize this design.

Colors

Designer to choose colors to be used in the design.

```html
<!DOCTYPE html>
<html lang="en">
<head>
<meta charset="utf-8">
<title>Greymarsh Contracts – Stationery</title>
<link href="https://fonts.googleapis.com/css2?family=Open+Sans:wght@400;600&family=Poppins:wght@400;600&display=swap" rel="stylesheet">
<style>
  :root{
    --ink:#2b2b2b;
    --text:#555555;
    --grey:#5c5c5c;
    --paper:#ffffff;
    --backdrop:#dcdcdc;
  }
  *{margin:0;padding:0;box-sizing:border-box}
  html,body{width:1200px;height:930px;overflow:hidden;background:var(--backdrop)}
  .canvas{position:relative;width:1200px;height:930px}

  /* Letterhead */
  .letterhead{position:absolute;left:104px;top:120px;width:530px;height:680px;background:var(--paper);
    font-family:"Open Sans",sans-serif;color:var(--text);box-shadow:0 2px 10px rgba(0,0,0,.18);overflow:hidden}
  .letterhead .brand{position:absolute;right:54px;top:34px;align-items:flex-end}
  .brand{display:flex;flex-direction:column;align-items:center;gap:6px}
  .brand-square{width:42px;height:42px;border:6px solid var(--ink)}
  .brand-name{font-family:"Open Sans",sans-serif;font-weight:600;color:var(--ink);font-size:12.5px;letter-spacing:1.2px;line-height:1.05;text-align:center}
  .letterhead .brand-square{margin-right:34px}
  .letter{position:absolute;left:50px;top:124px;width:428px;font-size:8.3px;line-height:15.1px}
  .letter p{margin-bottom:15px;text-align:justify}
  .letter .recipient{line-height:10.2px;margin:10px 0 34px;text-align:left}
  .letter .date{margin:0}
  .closing{margin-top:28px}
  .signature{width:122px;height:14px;margin:8px 0 6px;background:linear-gradient(90deg,#e9e9e9,#f4f4f4)}
  .signer-name{font-size:10.5px;color:#444;font-weight:600;line-height:14px}
  .signer-title{font-size:8.3px;line-height:13px}
  .letter-wave{position:absolute;left:0;bottom:0;width:530px;height:90px}
  .letter-contacts{position:absolute;right:56px;bottom:24px;text-align:right;color:#f2f2f2;font-size:8.3px;line-height:10.2px}
  .contact-row{display:flex;justify-content:flex-end;align-items:center;gap:6px}
  .contact-row svg{width:8px;height:8px;fill:#f2f2f2}

  /* Business cards */
  .card{position:absolute;left:768px;width:307px;height:175px;box-shadow:2px 2px 4px rgba(0,0,0,.35);overflow:hidden;font-family:"Poppins",sans-serif}
  .card-front{top:402px;background:var(--paper);color:var(--ink)}
  .card-back{top:623px;background:var(--ink);display:flex;align-items:center;justify-content:center}
  .holder{position:absolute;left:16px;top:13px}
  .holder-name{font-size:12.5px;font-weight:600;line-height:14px}
  .holder-title{font-size:8px;line-height:10px}
  .holder-contacts{position:absolute;left:16px;top:43px;font-size:8px;line-height:11.5px}
  .holder-contacts .contact-row{justify-content:flex-start;gap:3px}
  .holder-contacts svg{width:8px;height:8px;fill:var(--ink)}
  .holder-address{position:absolute;left:16px;top:71px;font-size:8px;line-height:10.4px}
  .holder-address strong{font-weight:600}
  .card-front .brand{position:absolute;left:165px;top:36px}
  .card-front .brand-square{width:36px;height:36px;border-width:5px}
  .card-front .brand-name{font-family:"Poppins",sans-serif;font-size:10.5px;letter-spacing:1px}
  .card-wave{position:absolute;left:0;bottom:0;width:307px;height:50px}
  .card-web{position:absolute;right:22px;bottom:10px;color:#f2f2f2;font-size:8.5px}
  .card-back .brand-square{border-color:var(--paper);width:46px;height:46px;border-width:6px}
  .card-back .brand-name{color:var(--paper);font-family:"Poppins",sans-serif;font-size:13px;letter-spacing:1.5px}
</style>
</head>
<body>
<div class="canvas">

  <section class="letterhead">
    <div class="brand">
      <div class="brand-square"></div>
      <div class="brand-name">GREYMARSH<br>CONTRACTS</div>
    </div>

    <div class="letter">
      <p class="date">Issuing Date: May 5, 2018</p>
      <p class="recipient">Name Of Employee Mr. XYZABC<br>Address of Employee<br>Address Line 2 etc..</p>
      <p>Dear Mr.XYZABC</p>
      <p>Lorem Ipsum has been the industry's standard dummy text ever since the 1500s, when an unknown printer took a galley of type and scrambled it to make a type specimen book. It has survived not only five centuries, but also the leap into electronic typesetting, remaining essentially unchanged. It was popularised in the 1960s with the release of Tessaprint sheets containing Lorem Ipsum passages, and more recently with desktop publishing software like Quillset Layout including versions of Lorem Ipsum.</p>
      <p>Lorem Ipsum is simply dummy text of the printing and typesetting industry. Lorem Ipsum has been the industry's standard dummy text ever since the 1500s, when an unknown printer took a galley of type and scrambled it to make a type specimen book.</p>
      <p>It has survived not only five centuries, but also the leap into electronic typesetting, remaining essentially unchanged. It was popularised in the 1960s with the release of Tessaprint sheets containing Lorem IpsumIpsum passages.</p>
      <div class="closing">Yours Sincerely</div>
      <div class="signature" role="img" aria-label="Handwritten signature of Marlen Okafor"></div>
      <div class="signer-name">Marlen Okafor</div>
      <div class="signer-title">Managing Director</div>
    </div>

    <svg class="letter-wave" viewBox="0 0 530 90" preserveAspectRatio="none" aria-hidden="true">
      <path d="M0,2 C60,32 160,42 240,38 C290,35 330,24 318,22 C240,32 120,32 0,16Z" fill="var(--grey)"/>
      <path d="M0,26 C110,56 210,56 310,38 C400,20 470,10 530,12 L530,90 L0,90Z" fill="var(--ink)"/>
    </svg>
    <div class="letter-contacts">
      <div class="contact-row">+91-22-28754193 <svg viewBox="0 0 10 10"><path d="M1 3h8l-1 5H2z M2 1h6v2H2z"/></svg></div>
      <div class="contact-row">kelvanjoshi@mailbrook.example <svg viewBox="0 0 10 10"><path d="M0 2h10v6H0z" /></svg></div>
      <div class="contact-row">www.greymarshcontracts.example <svg viewBox="0 0 10 10"><circle cx="5" cy="5" r="4.5"/></svg></div>
    </div>
  </section>

  <section class="card card-front">
    <div class="holder">
      <div class="holder-name">Kelvan Joshi</div>
      <div class="holder-title">Designated Partner</div>
    </div>
    <div class="holder-contacts">
      <div class="contact-row"><svg viewBox="0 0 10 10"><path d="M2 1h2l1 2-1 1c1 1 1 2 2 2l1-1 2 1v2H7C4 8 2 6 2 3z"/></svg>+91 97415 60382</div>
      <div class="contact-row"><svg viewBox="0 0 10 10"><path d="M0 2h10v6H0z"/></svg>kelvanjoshi@mailbrook.example</div>
    </div>
    <div class="holder-address">
      <strong>Greymarsh Engineering<br>Contracts LLP</strong><br>
      Block No.317, Wing C,<br>Tulvo Trade Court, Manek Pural Road,<br>Ruparel Industrial Estate,<br>Goregaon(E), Mumbai - 400 063
    </div>
    <div class="brand">
      <div class="brand-square"></div>
      <div class="brand-name">GREYMARSH<br>CONTRACTS</div>
    </div>
    <svg class="card-wave" viewBox="0 0 307 50" preserveAspectRatio="none" aria-hidden="true">
      <path d="M0,0 C30,14 80,18 130,16 C160,15 170,12 165,12 C120,16 60,16 0,8Z" fill="var(--grey)"/>
      <path d="M0,12 C60,28 120,26 170,18 C220,10 270,6 307,14 L307,50 L0,50Z" fill="var(--ink)"/>
    </svg>
    <div class="card-web">www.greymarshcontracts.example</div>
  </section>

  <section class="card card-back">
    <div class="brand">
      <div class="brand-square"></div>
      <div class="brand-name">GREYMARSH<br>CONTRACTS</div>
    </div>
  </section>

</div>
</body>
</html>
```